Heron Dusk business card design

I make handmade colourful women's beaded jewellery (necklaces and earnings).
I require a business card to be designed to truly reflect my jewellery, that is, it is different and stands out.
I would like the business card to look creative, arty, gentle and feminine and fit in with the look of my website and logo (already developed).
I would like the business card to have strong use of the water reeds that are flowing in the wind (please see the banner image on my website www.herondusk.net and attached files).

Target Market(s)

Women who are fashion conscious, hip and funky. My audience like things that are a little different and stand out in a crowd.These women are aged in their 20's-40's.

Industry/Entity Type

Jewelry

Contact Information for Business Card

Please include the following items:
1) my logo: Heron Dusk
2) my name, address and phone number: Darla Fontenot, Sydney, Australia, 0498 315 270
3) my web details: www.herondusk.net, info@herondusk.net, www.facebook.com/herondusk

Font styles to use
Other font styles liked:
• Remachine Script

Requirements
Must have
• My business card must have the following:
• 1) my personal details including all my website contacts (see above).
• 2) Heron Dusk logo
• 3) Reeds flowing in the wind (see my banner image on my website www.herondusk.net or see attached files).
Nice to have
• A sunrise in the background (rising over water)
• I would prefer that the colour scheme to fit with the Heron Dusk logo, that is the colours of an early morning sunrise i.e yellows, oranges. The use of black and white is fine.
Should not have
• I do not like a commercial manufactured look with hard edges. I would like a look that is soft and reflects an artistic, creative and independent business.

```html
<!DOCTYPE html>
<html lang="en">
<head>
<meta charset="utf-8">
<title>Heron Dusk – Business Card</title>
<link rel="stylesheet" href="https://fonts.googleapis.com/css2?family=Arimo:wght@400;700&display=swap">
<style>
  :root {
    --bg: #ece8e2;
    --ink: #231f20;
    --charcoal: #2b2a2a;
    --white: #ffffff;
    --sun-light: #fde7a6;
    --sun: #f7b21e;
    --amber: #e39a16;
    --reed: #6b3d12;
    --grey-text: #5c5c5c;
  }
  * { box-sizing: border-box; margin: 0; padding: 0; }
  html, body { width: 1200px; height: 950px; overflow: hidden; }
  body {
    background: var(--bg);
    font-family: "Arimo", Arial, sans-serif;
    position: relative;
  }
  .card {
    position: absolute;
    left: 250px;
    width: 700px;
    height: 400px;
    border-radius: 22px;
    overflow: hidden;
    box-shadow: 0 6px 18px rgba(0,0,0,0.18);
  }
  .card--front { top: 50px; }
  .card--back { top: 500px; background: var(--white); }

  /* Front */
  .reed-scene {
    position: absolute; inset: 0;
    background:
      radial-gradient(circle at 58% 55%, var(--sun-light) 0%, var(--sun) 38%, var(--amber) 75%, var(--reed) 130%);
  }
  .front-brand {
    position: absolute;
    left: 330px; top: 120px;
    display: flex; align-items: center; gap: 16px;
  }
  .brand-disc {
    width: 110px; height: 110px; border-radius: 50%;
    background: var(--sun);
    border: 5px solid var(--ink);
  }
  .brand-name {
    font-weight: 700; font-size: 34px; color: var(--ink);
  }
  .social-row {
    position: absolute; left: 380px; top: 268px;
    display: flex; gap: 10px;
  }
  .social-dot {
    width: 26px; height: 26px; border-radius: 50%;
    border: 2px solid var(--white);
  }

  /* Back */
  .back-shapes { position: absolute; inset: 0; }
  .holder {
    position: absolute; right: 36px; top: 30px; text-align: right;
    color: var(--white);
  }
  .holder-name { font-weight: 700; font-size: 22px; }
  .holder-role { font-size: 15px; margin-top: 4px; }
  .back-brand {
    position: absolute; left: 70px; top: 210px;
    display: flex; align-items: center; gap: 14px;
  }
  .back-brand .brand-disc { width: 96px; height: 96px; }
  .back-brand .brand-name { font-size: 28px; }
  .contact {
    position: absolute; left: 340px; top: 160px;
    color: var(--grey-text); font-size: 16px; line-height: 24px;
    list-style: none;
  }
  .contact li { display: flex; align-items: center; gap: 10px; }
  .contact .plain { padding-left: 0; }
  .contact-icon { width: 16px; height: 16px; flex: none; }
</style>
</head>
<body>

<section class="card card--front">
  <div class="reed-scene" role="img" aria-label="Silhouetted water reeds and bulrushes swaying against a golden sunrise"></div>
  <div class="front-brand">
    <span class="brand-disc"></span>
    <span class="brand-name">Heron Dusk</span>
  </div>
  <div class="social-row">
    <span class="social-dot"></span>
    <span class="social-dot"></span>
    <span class="social-dot"></span>
    <span class="social-dot"></span>
  </div>
</section>

<section class="card card--back">
  <svg class="back-shapes" viewBox="0 0 700 400" width="700" height="400" aria-hidden="true">
    <path d="M300 0 H700 V112 C590 104 430 70 300 0 Z" fill="var(--charcoal)"/>
    <path d="M370 66 C480 118 600 132 700 130" fill="none" stroke="var(--charcoal)" stroke-width="6"/>
    <path d="M0 130 C90 100 200 88 300 100 C180 118 70 175 0 320 Z" fill="var(--charcoal)"/>
    <path d="M0 335 C55 200 165 128 300 104 C190 145 95 215 40 400 H0 Z" fill="var(--sun)"/>
    <path d="M0 360 C40 250 120 175 230 132 C140 185 75 265 55 400 H0 Z" fill="var(--charcoal)"/>
  </svg>

  <div class="holder">
    <p class="holder-name">Marcus Bell</p>
    <p class="holder-role">President</p>
  </div>

  <div class="back-brand">
    <span class="brand-disc"></span>
    <span class="brand-name">Heron Dusk</span>
  </div>

  <ul class="contact">
    <li class="plain">Darla Fontenot</li>
    <li class="plain">Sydney, Australia</li>
    <li>
      <svg class="contact-icon" viewBox="0 0 16 16"><path d="M3 1 L6 1 L7 5 L5 6.5 C6 9 7 10 9.5 11 L11 9 L15 10 V13 C15 14 14 15 13 15 C6 15 1 10 1 3 C1 2 2 1 3 1 Z" fill="var(--ink)"/></svg>
      0498 315 270
    </li>
    <li>
      <svg class="contact-icon" viewBox="0 0 16 16"><rect x="1" y="3" width="14" height="10" fill="var(--ink)"/><path d="M1 3 L8 9 L15 3" fill="none" stroke="var(--white)" stroke-width="1.4"/></svg>
      info@herondusk.net
    </li>
    <li>
      <svg class="contact-icon" viewBox="0 0 16 16"><path d="M8 1 C5 1 3 3.2 3 6 C3 10 8 15 8 15 C8 15 13 10 13 6 C13 3.2 11 1 8 1 Z" fill="var(--ink)"/><circle cx="8" cy="6" r="2" fill="var(--white)"/></svg>
      www.herondusk.net
    </li>
    <li>
      <svg class="contact-icon" viewBox="0 0 16 16"><rect x="1" y="1" width="14" height="14" fill="var(--ink)"/></svg>
      herondusk
    </li>
  </ul>
</section>

</body>
</html>
```